2 x Digitize Logo | 2 x Business Cards | 2 x Fridge Magnets

We require 6 deliverables:
1. Residential logo redrawn (same just high quality for large print format).
2. Corporate logo redrawn (minor changes to wording and high quality for large print format).
3. New business card design for Furniture Removals (residential)
4. New business card design for Corporate Relocations (business)
5. New Fridge magnet for Furniture removals (residential)
6. New fridge magnet for Corporate Relocations (business)
1. Residential Logo
a. We require the logo to be translated into a high quality digital image with no modifications.
(see attached resilogo.jpg)
2. Residential Logo
a. We require the logo to be edited (add the word corporate relocations) be translated into a high quality digital image.
(see attached corplogo.jpg)
3. Using the resilogo please make a new business card for our business.
a. Please see the web site https://www.larkbendcarters.com.au for colours and inspiration.
b. The residential business card needs the following information:
i. Business Name (using the residential logo).
ii. Free Call: 1800 LB Cart (the L, B and Cart much be the same colour as the logo).
iii. Website: www.LarkbendCarters.com.au
iv. Address: 4/17 Ormsdale Court, VIC 3264
v. Email: cart@LarkbendCarters.com.au
vi. backof Card:
Review our service
www.PennantOrbit.com.au
Services: Local, Country, Interstate | Furniture Removals | Piano, Billiard Tables & Antiques
4. Using the corplogo please make a new business card for our business.
b. The corporate business card needs the following information:
i. Business Name (using the corporate logo).
v. Email: corporate@LarkbendCarters.com.au
vi. Back of Card:
Review our service
www.PennantOrbit.com.au
Services: Corporate relocations | Office equipment moves | Packing Service | Packing Materials
5. Using the resilogo please make a new fridge magent for our business.
b. The residential fidge magnet needs the following information:
iv. Services: Local, Country, Interstate | Furniture Removals | Piano, Billiard Tables & Antiques
6. Using the corplogo please make a new fridge magent for our business.
b. The corporate fidge magnet needs the following information:
iv. Services: Local, Country, Interstate | Corporate relocations
Target Market(s)
Residential Furniture Removals and Corporate Office relocations
Industry/Entity Type
Business
Contact Information for Business Card
Please see full brief for six items required
Requirements
Must have
- Clean simple, easy to read
Nice to have
- fresh, stand out, eye catching
Should not have
- plain, standard, boring, general

```html
<!DOCTYPE html>
<html lang="en">
<head>
<meta charset="utf-8">
<title>Larkbend Carters – Corporate Business Card</title>
<link href="https://fonts.googleapis.com/css2?family=Source+Sans+3:wght@400;600&display=swap" rel="stylesheet">
<style>
  :root {
    --stage: #121212;
    --paper: #ffffff;
    --brand-red: #c0120c;
    --brand-green: #02733b;
    --ink: #2a2a2a;
    --on-green: #ffffff;
  }
  * { box-sizing: border-box; margin: 0; padding: 0; }
  html, body { width: 1200px; height: 900px; overflow: hidden; }
  body {
    background: var(--stage);
    font-family: "Source Sans 3", "Myriad Pro", Arial, sans-serif;
    position: relative;
  }
  .card {
    position: absolute;
    top: 306px;
    width: 440px;
    height: 271px;
    overflow: hidden;
  }
  .card--front { left: 149px; background: var(--paper); }
  .card--back { left: 608px; background: var(--brand-green); color: var(--on-green); text-align: center; }

  .card__shapes { position: absolute; inset: 0; }

  .phone {
    position: absolute; left: 43px; top: 30px;
    font-size: 15px; color: var(--ink);
    display: flex; align-items: center; gap: 3px;
  }
  .phone__accent { color: var(--brand-red); }

  .brand {
    position: absolute; left: 236px; top: 80px;
    width: 180px;
    display: flex; align-items: center; gap: 6px;
    color: var(--brand-red);
    font-weight: 600;
    font-size: 14px;
    line-height: 1.15;
    text-transform: uppercase;
  }
  .brand__mark { width: 10px; height: 10px; background: var(--brand-red); flex: none; }

  .contacts {
    position: absolute; left: 22px; top: 163px;
    list-style: none;
    font-size: 14.5px; color: var(--ink);
  }
  .contacts li { display: flex; align-items: center; gap: 7px; height: 19px; }
  .contacts li:last-child { margin-top: 6px; }
  .contacts svg { width: 11px; height: 11px; fill: var(--brand-red); flex: none; }

  .review { position: absolute; top: 54px; left: 0; right: 0; }
  .review__label { font-size: 13px; }
  .review__url { font-size: 16px; margin-top: 2px; }

  .services { position: absolute; top: 146px; left: 0; right: 0; }
  .services__title {
    display: flex; align-items: center; justify-content: center; gap: 5px;
    font-size: 12.5px; text-transform: uppercase;
  }
  .services__title::before, .services__title::after {
    content: ""; width: 34px; height: 1px; background: var(--on-green);
  }
  .services__list { list-style: none; margin-top: 8px; font-size: 12.5px; line-height: 16px; text-transform: uppercase; }
</style>
</head>
<body>

<section class="card card--front" aria-label="Business card front">
  <svg class="card__shapes" viewBox="0 0 440 271" aria-hidden="true">
    <polygon points="0,22 14,22 20,61 0,61" fill="var(--brand-red)"/>
    <polygon points="15,22 33,22 33,61 21,61" fill="var(--brand-green)"/>
    <polygon points="0,251 238,251 226,271 0,271" fill="var(--brand-red)"/>
    <polygon points="248,244 440,244 440,271 230,271" fill="var(--brand-green)"/>
  </svg>

  <div class="phone">
    <svg width="11" height="11" viewBox="0 0 24 24" aria-hidden="true"><path fill="var(--brand-red)" d="M6.6 10.8a15 15 0 0 0 6.6 6.6l2.2-2.2a1 1 0 0 1 1-.25 11.4 11.4 0 0 0 3.6.6 1 1 0 0 1 1 1V20a1 1 0 0 1-1 1A17 17 0 0 1 3 4a1 1 0 0 1 1-1h3.5a1 1 0 0 1 1 1c0 1.25.2 2.45.6 3.6a1 1 0 0 1-.25 1z"/></svg>
    <span>1800 <span class="phone__accent">LB Cart</span></span>
  </div>

  <div class="brand">
    <span class="brand__mark"></span>
    <span>Larkbend Carters<br>Corporate Relocations</span>
  </div>

  <ul class="contacts">
    <li><svg viewBox="0 0 24 24" aria-hidden="true"><path d="M2 5h20v14H2zm2 2v.5l8 5 8-5V7z"/></svg>cart@LarkbendCarters.com.au</li>
    <li><svg viewBox="0 0 24 24" aria-hidden="true"><circle cx="12" cy="12" r="10"/></svg>www.LarkbendCarters.com.au</li>
    <li><svg viewBox="0 0 24 24" aria-hidden="true"><path d="M12 2a7 7 0 0 0-7 7c0 5 7 13 7 13s7-8 7-13a7 7 0 0 0-7-7zm0 9.5A2.5 2.5 0 1 1 12 6.5a2.5 2.5 0 0 1 0 5z"/></svg>4/17 Ormsdale Court, VIC 3264</li>
  </ul>
</section>

<section class="card card--back" aria-label="Business card back">
  <div class="review">
    <p class="review__label">Review our service</p>
    <p class="review__url">www.PennantOrbit.com.au</p>
  </div>
  <div class="services">
    <h2 class="services__title" style="font-weight:400">Services</h2>
    <ul class="services__list">
      <li>Corporate Relocations</li>
      <li>Office Equipment Moves</li>
      <li>Packing Service</li>
      <li>Packing Materials</li>
    </ul>
  </div>
</section>

</body>
</html>
```